Verodex business card

Business card for sustainable investment company called "Verodex". Verodex is an exchange platform selling carbon credits between buyers and sellers. Carbon Credits are an environmental commodity for reducing global carbon emissions.

the card should obviously have our logo and the theme should be sustainability/environment mixed with a trading platform.

Contact Information for Business Card

Logo, Name, Title, Phone, Email

Colors
0054AA
0677BA
7BADD7
CADEEF
E8F1F8
0094D4
00A9DD
6FCCEA
C7EBF8
E9F6FB
00AB8E
00BBA5
67D7C9
C6EFE9
E9F9F6
59FF00
82FF00
B8FF75
E3FFCB
F4FFEA

```html
<!DOCTYPE html>
<html lang="en">
<head>
<meta charset="utf-8">
<title>Verodex business card</title>
<link href="https://fonts.googleapis.com/css2?family=Inter:wght@400;600;700&display=swap" rel="stylesheet">
<style>
  :root {
    --backdrop: #949494;
    --card-light: #ebebeb;
    --card-navy: #0c2a52;
    --ink-navy: #112a4f;
    --ink-grey: #7a7a7a;
    --rule-grey: #b3b3b3;
    --accent-cyan: #00a9dd;
    --accent-blue: #0677ba;
    --white: #ffffff;
  }
  * { box-sizing: border-box; margin: 0; padding: 0; }
  html, body {
    width: 1200px; height: 1000px; overflow: hidden;
    background: var(--backdrop);
    font-family: "Inter", Arial, sans-serif;
  }
  .canvas { position: relative; width: 1200px; height: 1000px; }
  .card {
    position: absolute;
    width: 614px; height: 350px;
    border-radius: 28px;
  }
  .card--front { left: 288px; top: 141px; background: var(--card-light); }
  .card--back { left: 290px; top: 541px; background: var(--card-navy); }

  .brand {
    position: absolute; left: 39px; top: 50px;
    display: flex; align-items: center; gap: 14px;
  }
  .brand__square {
    width: 34px; height: 34px; border-radius: 4px;
    background: var(--accent-cyan);
  }
  .brand__name {
    font-weight: 700; font-size: 26px; letter-spacing: 0.2px;
    color: var(--ink-navy);
  }

  .person { position: absolute; left: 39px; top: 200px; }
  .person__name { font-weight: 700; font-size: 17px; color: var(--ink-navy); letter-spacing: 0.3px; }
  .person__title { font-weight: 400; font-size: 17px; color: var(--ink-grey); margin-top: 2px; letter-spacing: 0.5px; }

  .divider {
    position: absolute; left: 39px; top: 254px;
    width: 530px; height: 1.5px; background: var(--rule-grey);
  }

  .contact { position: absolute; font-size: 15.5px; color: var(--ink-grey); letter-spacing: 0.6px; }
  .contact__row { display: flex; align-items: center; gap: 8px; height: 23px; }
  .contact__icon { width: 15px; height: 15px; flex: none; }
  .contact--left { left: 39px; top: 265px; }
  .contact--right { right: 44px; top: 291px; }

  .back-name {
    position: absolute; right: 50px; bottom: 36px;
    font-weight: 700; font-size: 43px; color: var(--white); letter-spacing: 0.5px;
  }
</style>
</head>
<body>
<main class="canvas">
  <section class="card card--front" aria-label="Card front">
    <div class="brand">
      <span class="brand__square"></span>
      <span class="brand__name">VERODEX</span>
    </div>

    <div class="person">
      <p class="person__name">Name Surname</p>
      <p class="person__title">Title</p>
    </div>

    <div class="divider"></div>

    <div class="contact contact--left">
      <div class="contact__row">
        <svg class="contact__icon" viewBox="0 0 24 24" aria-hidden="true">
          <path fill="var(--accent-cyan)" d="M6.6 10.8a15.1 15.1 0 0 0 6.6 6.6l2.2-2.2a1 1 0 0 1 1-.25 11.4 11.4 0 0 0 3.6.57 1 1 0 0 1 1 1V20a1 1 0 0 1-1 1A17 17 0 0 1 3 4a1 1 0 0 1 1-1h3.5a1 1 0 0 1 1 1c0 1.25.2 2.45.57 3.57a1 1 0 0 1-.25 1z"/>
        </svg>
        <span>012•345•6789</span>
      </div>
      <div class="contact__row">
        <svg class="contact__icon" viewBox="0 0 24 24" aria-hidden="true">
          <rect x="2" y="5" width="20" height="14" rx="1.5" fill="var(--accent-cyan)"/>
          <path d="M3 6.5l9 6.5 9-6.5" fill="none" stroke="var(--white)" stroke-width="1.6"/>
        </svg>
        <span>name@website.com</span>
      </div>
    </div>

    <div class="contact contact--right">
      <div class="contact__row">
        <svg class="contact__icon" viewBox="0 0 24 24" aria-hidden="true">
          <g fill="none" stroke="var(--accent-cyan)" stroke-width="1.8">
            <circle cx="12" cy="12" r="9.5"/>
            <ellipse cx="12" cy="12" rx="4.2" ry="9.5"/>
            <path d="M2.5 12h19M4 7h16M4 17h16"/>
          </g>
        </svg>
        <span>website.com</span>
      </div>
    </div>
  </section>

  <section class="card card--back" aria-label="Card back">
    <p class="back-name">VERODEX</p>
  </section>
</main>
</body>
</html>
```